Redesign of outdated "Automotive Automation Company"

We are looking to finally update our outdated website with some cutting edge graphics. We want our customers to know we value technology and are cutting edge as far as design. We provide automation solutions for the automotive industry which essentially means we program robots, and sell automation related products.

Current URL

http://lnk.qorvi.example/Tm4pzr
Updates

Project Deadline Extended
Reason: The client portal wasn't working, it's just finally been fixed by Pixel Harbor. I will go through and start reviewing designs.

We are trying to go with the same look and feel on our business cards, line cards, apparel, etc. so we are forming a brand. I have included the current draft of the line card. Please utilize our newest Logo VEL Standardized Logo.jpg http://img.plomtra.example/zuKe9rb.jpg?1 Also we are trying hard to sell the following software / hardware companies so we can put some emphasis on their product. Corvane Systems https://www.corvanesystems.example/ We make money on selling the software and then on the integration. I think you should tie in this animation. ยท Shop Line Muddle to Momentum https://media.vuntelo.example/clips/9b2e7f1d04c3a85e6f2d1b7c9a0e4f3d8c6b2a1e.jpg?image_play_button=true&image_play_button_color=7b796ae0&image_crop_resized=275x155 In this 2-minute video, discover how Trellan can help run your plant floor. We are Authorized Integrators / Resellers for Pembry Controls Hadrix Sensorik http://hadrix.example/en/usa/ Corvane Systems https://www.corvanesystems.example/ Unified Motion Works www.umwkq.example Brisk Beltway Corp www.briskbeltway.example Castmere Fabrication http://www.castmerefab.example/strategic_partners.aspx

Target Market(s)

Large automotive companies looking for automation or robotic programming. So Professional is key.

Industry/Entity Type

Automotive

Font styles to use
Other font styles liked:
• Possible Open Sans or Lato

Colors
0591cc
ceeaf6
fbd4d5
fbf289
fece3e

Requirements
Must have
• Professional Modern Design.

I want a homepage design, and a rough Sales Page... Where numerous products can be listed.
Nice to have
• Maybe an updated logo if possible.

```html
<!DOCTYPE html>
<html lang="en">
<head>
<meta charset="utf-8">
<title>VEL Engineering Solutions</title>
<link href="https://fonts.googleapis.com/css2?family=Cinzel:wght@600;700&family=Montserrat:wght@600&family=Lato&family=Open+Sans&family=Arimo&family=Ubuntu&display=swap" rel="stylesheet">
<style>
:root{
  --navy:#0b2646;
  --blue-dark:#0c3563;
  --blue:#1c5f9c;
  --red:#e2143b;
  --gold:#d4b21c;
  --yellow:#fcc628;
  --orange:#f08a1c;
  --grey-band:#f1f1f1;
  --ring:#e6e6e6;
  --ink:#222;
  --text:#444;
  --white:#fff;
}
*{margin:0;padding:0;box-sizing:border-box}
html,body{width:791px;height:1200px;overflow:hidden;background:var(--white)}
body{position:relative;font-family:"Arimo",sans-serif;color:var(--ink)}
.topbar{position:absolute;left:0;top:0;width:791px;height:23px;background:var(--navy);font-size:9px;color:#9fb3c8}
.topbar .call{position:absolute;left:442px;top:6px}
.topbar .call b{color:var(--white);font-weight:normal;margin-left:4px}
.topbar .phone-ico{display:inline-block;width:5px;height:8px;border:1.5px solid var(--yellow);border-radius:1px;vertical-align:-1px;margin-left:3px}
.social{position:absolute;left:608px;top:6px;display:flex;gap:9px}
.social span{width:10px;height:10px;border-radius:50%;background:#c9d6e4}
.hero{position:absolute;left:0;top:23px;width:791px;height:354px;background:radial-gradient(ellipse at 62% 45%,#2c78b8 0%,#17528c 45%,var(--blue-dark) 100%)}
.brand{position:absolute;left:82px;top:48px;display:flex;align-items:center;gap:8px}
.brand .dot{width:34px;height:34px;border-radius:50%;background:var(--red)}
.brand .name{font-family:"Cinzel",serif;font-weight:700;font-size:15px;color:var(--white);line-height:1.15}
.nav{position:absolute;left:384px;top:48px;display:flex;font-family:"Montserrat",sans-serif;font-size:10.5px;color:var(--white)}
.nav a{color:inherit;text-decoration:none;height:22px;line-height:22px;padding:0 9px;margin-right:19px}
.nav a.active{background:var(--red);border-radius:2px}
.nav a:last-child{margin-right:0}
.nav-rule{position:absolute;left:360px;top:76px;width:360px;height:1px;background:rgba(255,255,255,.3)}
.robot{position:absolute;left:288px;top:72px;width:442px;height:276px;border-radius:40% 45% 20% 20%;background:radial-gradient(ellipse at 55% 40%,#f2f4f6 0%,#c9d2da 40%,rgba(60,110,160,0) 72%)}
.hero h1{position:absolute;left:66px;top:176px;font-family:"Cinzel",serif;font-weight:700;font-size:27px;color:var(--white);letter-spacing:1px}
.hero .tag{position:absolute;left:68px;top:219px;font-family:"Cinzel",serif;font-weight:600;font-size:11.5px;line-height:17px;color:var(--white);letter-spacing:.8px}
.cta{position:absolute;left:66px;top:271px;width:185px;height:40px;background:var(--gold);border-radius:4px;box-shadow:0 3px 0 #8e7510;font-family:"Cinzel",serif;font-weight:700;font-size:16px;color:var(--white);text-align:center;line-height:40px;letter-spacing:1px}
.intro{position:absolute;left:0;top:377px;width:791px;height:141px;background:var(--grey-band);padding:18px 66px 0}
.intro h2{font-family:"Montserrat",sans-serif;font-weight:600;font-size:16.5px;color:#111}
.intro .sub{font-family:"Lato",sans-serif;font-size:12.5px;color:var(--orange);margin-top:6px}
.intro p{font-family:"Open Sans",sans-serif;font-size:9.6px;line-height:16.5px;color:var(--text);margin-top:12px;text-indent:18px;position:relative}
.intro p:before{content:"\201C";position:absolute;left:-18px;top:-6px;font-size:24px;color:#888;font-family:Georgia,serif}
.badges{position:absolute;left:0;top:548px;width:791px;height:210px}
.badge{position:absolute;top:0;width:200px;height:210px}
.badge .ring{position:absolute;left:15px;top:35px;width:170px;height:170px;border-radius:50%;background:var(--ring)}
.badge .photo{position:absolute;left:24px;top:44px;width:152px;height:152px;border-radius:50%}
.overview{position:absolute;left:0;top:808px;width:791px;text-align:center;font-family:"Cinzel",serif;font-weight:700;font-size:27px;color:var(--red);letter-spacing:1.5px}
.rule1{position:absolute;left:165px;top:848px;width:413px;height:1px;background:#bbb}
.rule2{position:absolute;left:137px;top:856px;width:507px;height:1px;background:#bbb}
.feature{position:absolute;width:300px}
.feature .icon{position:absolute;left:0;top:0;width:64px;height:64px;border-radius:50%;border:2px solid var(--yellow);padding:3px}
.feature .icon div{width:100%;height:100%;border-radius:50%;background:var(--yellow);display:flex;align-items:center;justify-content:center}
.feature h3{position:absolute;left:80px;top:0;font-family:"Arimo",sans-serif;font-weight:normal;font-size:12.5px;color:#111;white-space:nowrap}
.feature p{position:absolute;left:80px;top:20px;width:235px;font-size:9.2px;line-height:14.5px;color:#333}
.footer{position:absolute;left:0;top:1133px;width:791px;height:67px;background:linear-gradient(90deg,#0c3563,#1a5590)}
.footer .links{position:absolute;left:69px;top:15px;font-size:10px;color:var(--white)}
.footer .links span{margin:0 9px;opacity:.8}
.footer .copy{position:absolute;left:69px;top:37px;font-size:9px;color:#dfe8f1}
.footer .mini{position:absolute;left:612px;top:22px;display:flex;align-items:center;gap:5px;font-family:"Cinzel",serif;font-weight:700;font-size:9px;color:var(--white)}
.footer .mini i{width:16px;height:16px;border-radius:50%;background:var(--red)}
</style>
</head>
<body>
<div class="topbar">
  <div class="call">Call Us: <span class="phone-ico"></span><b>+990 555 014 200</b></div>
  <div class="social" aria-label="Social links"><span></span><span></span><span></span><span></span><span></span><span></span></div>
</div>

<header class="hero">
  <div class="brand"><div class="dot"></div><div class="name">VEL Engineering<br>Solutions</div></div>
  <nav class="nav"><a class="active" href="#">HOME PAGE</a><a href="#">SERVICES</a><a href="#">CONTACT</a><a href="#">ABOUT</a></nav>
  <div class="nav-rule"></div>
  <div class="robot" role="img" aria-label="White humanoid robot crouching on one hand"></div>
  <h1>Your Premier</h1>
  <div class="tag">Automation Consulting &amp;<br>Systems Integration choice!</div>
  <div class="cta">1-877-MOTION-8</div>
</header>

<section class="intro">
  <h2>Your Premier Automation Consulting &amp; Systems Integration choice!</h2>
  <div class="sub">Helping your business optimize its Automation....</div>
  <p>Industrial Automation is constantly evolving with ever-changing technological breakthroughs. For companies to remain competitive, they need to be more nimble than ever implementing productivity and manufacturing innovations. But identifying and implementing the right Automation, Robotics and industrial Controls is never easy. That's where our team of experts comes in to play bringing our proven experience to the table.</p>
</section>

<section class="badges">
  <div class="badge" style="left:55px">
    <svg width="200" height="80" style="position:absolute;left:0;top:0"><defs><path id="arc1" d="M12,100 A88,88 0 0 1 188,100"/></defs><text font-family="Ubuntu,sans-serif" font-size="13.5" fill="#e2143b"><textPath href="#arc1" startOffset="50%" text-anchor="middle">Get to know our Team approach</textPath></text></svg>
    <div class="ring"></div>
    <div class="photo" role="img" aria-label="Silhouettes of a business team in front of a world map" style="background:linear-gradient(180deg,#d9dde3,#8a929c)"></div>
  </div>
  <div class="badge" style="left:293px">
    <svg width="200" height="80" style="position:absolute;left:0;top:0"><defs><path id="arc2" d="M12,100 A88,88 0 0 1 188,100"/></defs><text font-family="Ubuntu,sans-serif" font-size="13.5" fill="#e2143b"><textPath href="#arc2" startOffset="50%" text-anchor="middle">This way to Automation success</textPath></text></svg>
    <div class="ring"></div>
    <div class="photo" role="img" aria-label="Businessman facing a sketched business plan on a blue wall" style="background:linear-gradient(180deg,#5d93d6,#2f5f9e)"></div>
  </div>
  <div class="badge" style="left:530px">
    <svg width="200" height="80" style="position:absolute;left:0;top:0"><defs><path id="arc3" d="M12,100 A88,88 0 0 1 188,100"/></defs><text font-family="Ubuntu,sans-serif" font-size="13.5" fill="#e2143b"><textPath href="#arc3" startOffset="50%" text-anchor="middle">Bring great ideas to your business</textPath></text></svg>
    <div class="ring"></div>
    <div class="photo" role="img" aria-label="Hand holding a glowing globe of light bulbs" style="background:radial-gradient(circle at 40% 40%,#bfe0ff,#2b5f99 60%,#1a2a44)"></div>
  </div>
</section>

<h2 class="overview">Overview VEL</h2>
<div class="rule1"></div><div class="rule2"></div>

<div class="feature" style="left:65px;top:899px">
  <div class="icon"><div><svg width="30" height="30" viewBox="0 0 30 30"><path d="M6 24 L22 6 L25 9 L9 27 Z" fill="#111"/><path d="M6 6 L24 24" stroke="#111" stroke-width="3"/></svg></div></div>
  <h3>APPLICATIONS ENGINEERING</h3>
  <p>Provide electrical and mechanical expertise to solve automation specific application problems by utilizing best known industry practices.</p>
</div>
<div class="feature" style="left:409px;top:899px">
  <div class="icon" style="top:12px"><div><svg width="30" height="30" viewBox="0 0 30 30"><circle cx="11" cy="11" r="6" fill="none" stroke="#111" stroke-width="4" stroke-dasharray="3 2"/><circle cx="20" cy="20" r="5" fill="none" stroke="#111" stroke-width="4" stroke-dasharray="3 2"/></svg></div></div>
  <h3 style="left:85px">DESIGN ENGINEERING</h3>
  <p style="left:85px">Provide electro-mechanical designs for machine down-time improvements and cost reductions. Perform sizing calculations for motion control and fluid power applications.</p>
</div>
<div class="feature" style="left:66px;top:1005px">
  <div class="icon"><div><svg width="30" height="30" viewBox="0 0 30 30"><path d="M17 4 L9 17 H15 L12 26 L21 13 H15 Z" fill="#111"/><circle cx="15" cy="15" r="12" fill="none" stroke="#111" stroke-width="2" stroke-dasharray="3 4"/></svg></div></div>
  <h3>DESIGN SPECIFICATION</h3>
  <p>Develop controls and mechanical specifications for machines to be used when purchasing equipment. Collaborate with the systems integrator / machine OEM to ensure adherence to machine specifications.</p>
</div>
<div class="feature" style="left:413px;top:1009px">
  <div class="icon" style="top:10px"><div><svg width="32" height="32" viewBox="0 0 32 32" fill="none" stroke="#111" stroke-width="2.5"><circle cx="16" cy="11" r="7"/><circle cx="11" cy="20" r="7"/><circle cx="21" cy="20" r="7"/></svg></div></div>
  <h3 style="left:84px">ELECTRICAL ENGINEERING</h3>
  <p style="left:84px">Provide electro-mechanical designs for machine down-time improvements and cost reductions. Perform sizing calculations for motion control and fluid power applications.</p>
</div>

<footer class="footer">
  <div class="links">Home Page<span>|</span>Services<span>|</span>Contact<span>|</span>About Us</div>
  <div class="copy">Content copyright 2015. VEL Engineering Solutions . All rights reserved.</div>
  <div class="mini"><i></i>VEL Engineering</div>
</footer>
</body>
</html>
```